Agriculture farming Hemp and CBD

The logo is in works with your company now, should be ready in a few days. We have our Domain (kestrelbrookhollow.com) We would like to see incorporated seed to growth, but not necessary. we would like to nature colors and some black and green. we have our farm and will be growing and selling HEMP and CBD we are based in the state of Virginia. Would like to incorporate the words pause, play, rewind if possible but not necessary.

Target Market(s)

20 years old to elderly

Coding

Coded - Design and coding required

Number of Pages Required

3 page

Font styles to use
Serif

Requirements
Must have
• I'm not sure on the must haves, we are open to any ideas, we would definitely like to see Hemp and CBD included, may the life cycle of seed to plant. We must have a pop up asking if you are 20 years old before they can enter our site and to view or purchase our product. I want the design to be totally different than what i uploaded.
Nice to have
• Would like to see natural colors as well as black and green
Should not have
• I want

```html
<!DOCTYPE html>
<html lang="en">
<head>
<meta charset="utf-8">
<title>Kestrel Brook Hollow — Hemp &amp; CBD</title>
<link rel="stylesheet" href="https://fonts.googleapis.com/css2?family=Montserrat:wght@400;500;600;700;800&family=Arimo:wght@400;700&display=swap">
<style>
:root{
  --black:#000;
  --green:#3f9a1e;
  --green-dark:#2f7d12;
  --green-band:#419b20;
  --brown:#5a2f0e;
  --gold:#e6a83a;
  --gold-light:#f2c45a;
  --cream:#f0e7e4;
  --text:#555;
  --white:#fff;
}
*{margin:0;padding:0;box-sizing:border-box}
html,body{width:1200px;height:3216px;overflow:hidden;background:var(--white)}
body{position:relative;font-family:"Arimo",Arial,sans-serif;color:var(--text)}
.abs{position:absolute}

/* header */
.site-header{left:0;top:0;width:1200px;height:109px;background:var(--black)}
.brand{left:52px;top:30px;font-family:"Montserrat",sans-serif;font-weight:700;font-size:27px;color:var(--white);letter-spacing:-.3px}
.contact-line{top:15px;font-size:12px;color:var(--white);display:flex;align-items:center;gap:7px;white-space:nowrap}
.contact-line b{font-weight:700}
.contact-line svg{width:16px;height:16px}
.main-nav a{position:absolute;top:66px;font-family:"Montserrat",sans-serif;font-size:12px;color:var(--white);text-decoration:none;letter-spacing:.2px;white-space:nowrap}
.main-nav a.active{color:var(--green)}
.nav-underline{left:500px;top:105px;width:38px;height:3px;background:var(--white)}

/* hero */
.hero{left:0;top:109px;width:1200px;height:577px;background:radial-gradient(ellipse at 70% 50%,#f6e27e 0%,#f2dc6a 55%,#e9cf58 100%)}
.hero-panel{left:70px;top:262px;width:455px;height:240px;background:rgba(56,140,28,.92);clip-path:polygon(0 0,100% 0,100% 78%,88% 100%,0 100%)}
.hero-title{left:109px;top:300px;font-family:"Montserrat",sans-serif;font-weight:700;font-size:27px;line-height:35px;letter-spacing:-.8px;color:var(--white);white-space:nowrap}
.hero-text{left:110px;top:379px;width:400px;font-size:12.5px;line-height:20px;color:var(--white)}
.btn-gold{background:linear-gradient(180deg,var(--gold-light),var(--gold));color:var(--white);font-family:"Montserrat",sans-serif;font-weight:700;font-size:12px;border-radius:22px;display:flex;align-items:center;justify-content:center;letter-spacing:.3px}
.hero-btn{left:104px;top:429px;width:140px;height:42px}
.dot{top:647px;width:12px;height:12px;border-radius:50%;border:2px solid var(--white)}
.dot.on{background:var(--white)}

/* category tiles */
.tile{top:696px;height:347px}
.tile-photo{position:absolute;left:0;top:0;width:100%;height:277px}
.tile-label{position:absolute;left:0;bottom:0;width:100%;height:70px;display:flex;align-items:center;justify-content:center;font-family:"Montserrat",sans-serif;font-weight:800;font-size:34px;color:var(--white)}

/* welcome */
.eyebrow{left:0;top:1090px;width:1200px;text-align:center;font-family:"Montserrat",sans-serif;font-size:22px;color:var(--green)}
.about-title{left:0;top:1132px;width:1200px;text-align:center;font-family:"Montserrat",sans-serif;font-weight:800;font-size:36px;line-height:44px;color:var(--black)}
.about-text{left:210px;top:1240px;width:780px;text-align:center;font-size:15.5px;line-height:25.5px;color:#666}
.btn-outline{left:505px;top:1370px;width:178px;height:48px;border:2px solid var(--green);border-radius:24px;display:flex;align-items:center;justify-content:center;font-family:"Montserrat",sans-serif;font-weight:700;font-size:14px;color:var(--green-dark)}

/* why */
.why{left:0;top:1479px;width:1200px;height:553px;background:var(--cream)}
.why-photo{left:0;top:1479px;width:690px;height:553px;background:linear-gradient(90deg,#8f7a3e 0%,#b59a3f 40%,#c9b860 70%,rgba(240,231,228,0) 100%)}
.why-title{left:638px;top:1625px;font-family:"Montserrat",sans-serif;font-weight:700;font-size:30px;color:var(--black)}
.why-sub{left:638px;top:1680px;font-size:18px;color:#222}
.why-text{left:641px;top:1723px;width:490px;font-size:13.5px;line-height:24.5px;color:#666}
.why-btn{left:638px;top:1852px;width:168px;height:43px}

/* blog */
.blog-title{left:0;top:2075px;width:1200px;text-align:center;font-family:"Montserrat",sans-serif;font-weight:700;font-size:30px;color:var(--black)}
.green-band{left:0;top:2436px;width:1200px;height:580px;background:var(--green-band)}
.card{top:2156px;width:315px;height:382px;background:var(--white);text-align:center}
.card.featured{background:var(--brown)}
.card-photo{position:absolute;left:0;top:0;width:100%;height:192px}
.card-date{position:absolute;left:0;top:222px;width:100%;font-family:"Montserrat",sans-serif;font-size:12.5px;color:#4c6b1a}
.card-heading{position:absolute;left:0;top:245px;width:100%;font-family:"Montserrat",sans-serif;font-weight:600;font-size:16px;color:var(--black)}
.card-text{position:absolute;left:22px;top:282px;width:271px;font-family:"Montserrat",sans-serif;font-size:11.2px;line-height:20px;color:#444}
.card-link{position:absolute;left:0;top:344px;width:100%;font-family:"Montserrat",sans-serif;font-weight:700;font-size:10px;color:var(--gold)}
.card.featured .card-date,.card.featured .card-heading,.card.featured .card-link{color:var(--white)}
.card.featured .card-text{color:#e8d7c8}
.card.featured .card-date{top:218px}
.card.featured .card-heading{top:240px}
.card.featured .card-text{top:278px}
.card.featured .card-link{top:340px}

/* contact */
.contact-title{left:0;top:2596px;width:1200px;text-align:center;font-family:"Montserrat",sans-serif;font-weight:700;font-size:34px;color:var(--white)}
.contact-sub{left:0;top:2647px;width:1200px;text-align:center;font-size:13.5px;color:var(--white)}
.field{background:var(--white);font-family:"Montserrat",sans-serif;font-size:13px;color:#555;padding:0 0 0 22px;display:flex;align-items:center}
.field.message{align-items:flex-start;padding-top:14px}
.send{left:536px;top:2908px;width:116px;height:40px;border-radius:20px;background:var(--black);color:var(--white);font-family:"Montserrat",sans-serif;font-weight:700;font-size:12.5px;display:flex;align-items:center;justify-content:center}

/* footer */
.site-footer{left:0;top:3016px;width:1200px;height:200px;background:var(--black)}
.footer-nav a{position:absolute;top:3071px;font-family:"Montserrat",sans-serif;font-weight:500;font-size:12.5px;color:var(--white);text-decoration:none;white-space:nowrap}
.copyright{left:0;top:3103px;width:1200px;text-align:center;font-size:11px;color:#bbb}
.social{top:3141px;width:30px;height:30px;border-radius:50%;background:var(--gold-light)}
.social.first{background:#23a31a}
</style>
</head>
<body>

<header class="abs site-header"></header>
<div class="abs brand">kestrelbrookhollow.com</div>

<div class="abs contact-line" style="left:674px">
  <svg viewBox="0 0 16 16"><circle cx="8" cy="8" r="8" fill="#fff"/><rect x="4" y="5" width="8" height="6" rx="1" fill="#000"/><path d="M4.5 5.5 8 8.3 11.5 5.5" stroke="#fff" stroke-width="1" fill="none"/></svg>
  <span><b>Email us:</b> hello@kestrelbrookhollow.com</span>
</div>
<div class="abs contact-line" style="left:944px">
  <svg viewBox="0 0 16 16"><circle cx="8" cy="8" r="8" fill="#fff"/><path d="M5 4.2c.5-.4 1-.3 1.3.2l.8 1.3c.2.4.1.8-.2 1.1l-.5.4c.5 1 1.3 1.8 2.3 2.3l.4-.5c.3-.3.7-.4 1.1-.2l1.3.8c.5.3.6.8.2 1.3-.7.9-1.6 1.2-2.7.7C7 10.8 5.2 9 4.4 7 3.9 5.8 4.2 4.9 5 4.2z" fill="#000"/></svg>
  <span><b>Call Today: (555) 014 2290</b></span>
</div>

<nav class="main-nav">
  <a class="active" style="left:499px">HOME</a>
  <a style="left:583px">ABOUT US</a>
  <a style="left:691px">CBD</a>
  <a style="left:763px">HEMP</a>
  <a style="left:844px">BLOGS</a>
  <a style="left:931px">RESOURCES</a>
  <a style="left:1049px">CONTACT US</a>
</nav>
<div class="abs nav-underline"></div>

<section class="abs hero" role="img" aria-label="CBD oil bottles, droppers and hemp leaves on a yellow surface"></section>
<div class="abs hero-panel"></div>
<h1 class="abs hero-title">AULTRICIES ORCI FEUGIAT<br>SUSCIPIT LEO MASSA</h1>
<p class="abs hero-text">Curabitur vel dolor ultrices ipsum dictum tristique Praesent vitae lacus Ut velit enim vestibulum non fermentum nec hendrerit</p>
<div class="abs btn-gold hero-btn">CONTACT US&nbsp;›</div>
<span class="abs dot on" style="left:567px"></span>
<span class="abs dot" style="left:593px"></span>
<span class="abs dot" style="left:618px"></span>

<a class="abs tile" style="left:9px;width:594px">
  <div class="tile-photo" role="img" aria-label="Hemp field under a blue sky" style="background:linear-gradient(180deg,#7fb6e8 0%,#a9cfe9 40%,#5f8f2c 62%,#3f6e1c 100%)"></div>
  <div class="tile-label" style="background:var(--brown)">HEMP</div>
</a>
<a class="abs tile" style="left:610px;width:581px">
  <div class="tile-photo" role="img" aria-label="Dropper releasing CBD oil into a glass bottle among hemp leaves" style="background:radial-gradient(ellipse at 40% 50%,#9db86a 0%,#5e7f2f 55%,#2f4d18 100%)"></div>
  <div class="tile-label" style="background:var(--green-dark)">CBD</div>
</a>

<div class="abs eyebrow">— WELCOME TO —</div>
<h2 class="abs about-title">ABOUT KESTREL BROOK<br>HOLLOW</h2>
<p class="abs about-text">Curabitur vel dolor ultrices ipsum dictum tristique Praesent vitae lacus Ut velit enim vestibulum non fermen­tum nec hendrerit quis leo Pellentesque rutrum malesuada neque Nunc tempus felis vitae urna Vivamus porttitor neque at volutpat rutrum purus nisi eleifend libero a tempus libero lectus feugiat felis Morbi diam mauris viverra in gravida eu mattis in</p>
<div class="abs btn-outline">LEARN MORE</div>

<section class="abs why"></section>
<div class="abs why-photo" role="img" aria-label="Hemp seeds in a wooden scoop, hemp powder and a carafe of oil"></div>
<h2 class="abs why-title">Why We Are</h2>
<p class="abs why-sub">Pellentesque rutrum malesuada neque</p>
<p class="abs why-text">Curabitur vel dolor ultrices ipsum dictum tristique Praesent vitae lacus Ut velit enim vestibulum non fermentum nec hendrerit quis leo Pellentesque rutrum malesuada neque Nunc tempus felis vitae urna Vivamus porttitor neque at vo­lutpat rutrum purus nisi eleifend libero a tempus libero</p>
<div class="abs btn-gold why-btn" style="font-size:13px">LEARN MORE</div>

<h2 class="abs blog-title">Latest Blog Posts</h2>
<div class="abs green-band"></div>

<article class="abs card" style="left:117px">
  <div class="card-photo" role="img" aria-label="CBD cream jar, tube and oil bottle with hemp leaves" style="background:linear-gradient(135deg,#eef0ec 0%,#b9cdb4 55%,#8fae86 100%)"></div>
  <div class="card-date">25 Aug 2020</div>
  <h3 class="card-heading">Lorem ipsum blog heading</h3>
  <p class="card-text">Fusce ultricies orci ac feugiat suscipit leo massa sodales velit et scelerisque mi tortor at ipsum Proin orci odio commodo ac gravida non</p>
  <div class="card-link">LEARN MORE</div>
</article>
<article class="abs card featured" style="left:447px">
  <div class="card-photo" role="img" aria-label="Close-up of a hemp leaf" style="background:radial-gradient(ellipse at 50% 45%,#7fc23a 0%,#3f8a1c 55%,#1f4d0e 100%)"></div>
  <div class="card-date">25 Aug 2020</div>
  <h3 class="card-heading">Lorem ipsum blog heading</h3>
  <p class="card-text">Fusce ultricies orci ac feugiat suscipit leo massa sodales velit et scelerisque mi tortor at ipsum Proin orci odio commodo ac gravida non</p>
  <div class="card-link">LEARN MORE</div>
</article>
<article class="abs card" style="left:778px">
  <div class="card-photo" role="img" aria-label="CBD oil bottles and jars on a wooden table with hemp plants behind" style="background:linear-gradient(180deg,#4e7a2c 0%,#6f9a3e 55%,#b19a5a 80%,#8a6f3e 100%)"></div>
  <div class="card-date" style="top:224px">25 Aug 2020</div>
  <h3 class="card-heading" style="top:247px">Lorem ipsum blog heading</h3>
  <p class="card-text" style="top:284px">Fusce ultricies orci ac feugiat suscipit leo massa sodales velit et scelerisque mi tortor at ipsum Proin orci odio commodo ac gravida non</p>
  <div class="card-link" style="top:346px">LEARN MORE</div>
</article>

<h2 class="abs contact-title">Get in touch with us</h2>
<p class="abs contact-sub">Aectus feugiat felis Morbi diam mauris viverra in gravida eu mattis in Curabitur</p>
<div class="abs field" style="left:250px;top:2695px;width:343px;height:43px">First Name*</div>
<div class="abs field" style="left:603px;top:2695px;width:344px;height:43px">Last Name*</div>
<div class="abs field" style="left:250px;top:2748px;width:343px;height:43px">Email *</div>
<div class="abs field" style="left:603px;top:2748px;width:344px;height:43px">Phone*</div>
<div class="abs field message" style="left:250px;top:2802px;width:697px;height:86px">Message</div>
<div class="abs send">SEND</div>

<footer class="abs site-footer"></footer>
<nav class="footer-nav">
  <a style="left:257px">HOME</a>
  <a style="left:341px">ABOUT US</a>
  <a style="left:449px">PRODUCTS</a>
  <a style="left:562px">SHOP</a>
  <a style="left:643px">BLOGS</a>
  <a style="left:730px">TESTIMONIALS</a>
  <a style="left:866px">CONTACT</a>
</nav>
<p class="abs copyright">© Copyright 2020 . Kestrel Brook Hollow . All Right Reserved</p>
<span class="abs social first" style="left:518px"></span>
<span class="abs social" style="left:557px"></span>
<span class="abs social" style="left:595px"></span>
<span class="abs social" style="left:632px"></span>

</body>
</html>
```